Single Page Corporate Profile Web-site Design

We're a new IT Resourcing company called vantyx, and we need a ew single page corporate web-site to establish our credentials.

Our model is to extend IT resourcing to offer access to global resources, end to end management, and a structured approach resourcing process.

Phase 2 (out of scope) will be a full site build in approximately a month's time.

This project is to:
- Establish a look and feel for web, consistent with existing design work (logo an corporate presentation)
- Build the web pages
- Upload onto our domain hosting site (K&Q)

The web-site:
We want a modern, clean and bold design.

We'd like a design that is consistent with our corporate presentation (sourceless supplied). In terms of look and feel and use of graphics.

KEY FEATURES
- Single page design.
- Navigation bar (to page sections) at the top of the page.
- No cookies (phase 1 design)
- Good example of preferred web page design:
www.plomvex42.com
https://brisq.com/dial/days-with-brisq-dial/
http://www.talwickmachines.com
- Clear sections on page as structured in the attached slides.
- We would like some of the page sections to use imagery of your choice - but please no cliched "IT people" or "data-centre" images.
- Image use must be royalty free.

ANY ADVICE WELCOME ! It's been a while since we've done this.

Target Market(s)

Companies - mid-size, technically sophisticated IT developers.
Potential employees

Industry/Entity Type

It Company

Number of Pages Required

1 page

Font styles to use
Other font styles liked:
• calibri

Requirements
Must have
• Do's
• - Please use graphics and "look and feel" provided
• - Follow similar style of those sites provided
• - Take the provided content and develop it for the web
• - Page must load quickly (if you think there's too much on the page - say so, and we'll put it across a few"
• - Please use background imagery for some of the sections
Should not have
• Don'ts
• - Please don't use cliched imagery e.g. "IT people" or "data-centre lights"
• - Use dark colours

```html
<!DOCTYPE html>
<html lang="en">
<head>
<meta charset="utf-8">
<title>vantyx – IT Resourcing</title>
<link href="https://fonts.googleapis.com/css2?family=Ubuntu:wght@400;500;700&family=Open+Sans:wght@400;600;700&display=swap" rel="stylesheet">
<style>
:root{
  --blue:#1f7fe0;
  --navy:#1e3796;
  --navy-deep:#172c7c;
  --orange:#ec7a1c;
  --ink:#2b2b2b;
  --grey:#6c6c6c;
  --light:#f2f2f2;
  --dark:#15181d;
  --dark-2:#22262d;
  --line:#d6d6d6;
  --white:#ffffff;
}
*{box-sizing:border-box;margin:0;padding:0}
html,body{width:1200px;height:4412px;overflow:hidden}
body{font-family:"Open Sans",Arial,sans-serif;color:var(--ink);background:var(--white);font-size:13px}
h1,h2,h3,h4{font-family:"Ubuntu",Arial,sans-serif;font-weight:500}
section,header,footer{position:relative;width:1200px;overflow:hidden}
.section-title{text-align:center;font-size:30px;letter-spacing:1px;text-transform:uppercase}
.section-lead{text-align:center;font-size:13px;color:var(--grey);line-height:24px;margin-top:14px}

/* header */
.site-header{height:118px;display:flex;align-items:center;justify-content:space-between;padding:0 86px 0 112px;background:var(--white)}
.brand{display:flex;flex-direction:column}
.brand-name{font-family:"Ubuntu",sans-serif;font-weight:700;font-size:46px;color:var(--navy);line-height:1}
.brand-tag{font-family:"Ubuntu",sans-serif;font-size:14px;color:var(--navy);margin-top:2px}
.nav{display:flex;gap:34px}
.nav a{font-family:"Ubuntu",sans-serif;font-size:13px;text-transform:uppercase;color:var(--navy);text-decoration:none}
.nav a.active{border-bottom:2px solid var(--blue);padding-bottom:4px}

/* hero */
.hero{height:579px;background:linear-gradient(180deg,#2c2f36 0%,#5a4e49 35%,#b5784f 52%,#3f3c3c 70%,#1b1d22 100%)}
.hero-lines{position:absolute;top:242px;width:100%;text-align:center}
.hero-lines p{font-family:"Ubuntu",sans-serif;font-weight:500;font-size:44px;color:var(--white);letter-spacing:1px;line-height:68px;text-transform:uppercase}
.hero-lines span{color:var(--orange);font-size:34px;margin:0 10px}
.hero-dots{position:absolute;bottom:22px;left:0;width:100%;display:flex;justify-content:center;gap:10px}
.hero-dots i{width:9px;height:9px;border-radius:50%;background:rgba(255,255,255,.4)}
.hero-dots i.on{background:var(--white)}

/* iteration */
.iteration{height:385px;background:var(--navy);color:var(--white)}
.iteration .section-title{padding-top:46px;font-size:28px}
.iteration .section-lead{color:#c7d1f0;margin-top:6px}
.benefits{display:flex;justify-content:space-between;padding:26px 120px 0}
.benefit{width:300px;text-align:center}
.benefit .icon{width:96px;height:96px;margin:0 auto}
.benefit h3{font-size:16px;margin-top:14px;text-transform:uppercase}
.benefit p{font-size:12px;line-height:20px;color:#c7d1f0;margin-top:8px}

/* services */
.services{height:527px;background:var(--white)}
.services .section-title{padding-top:36px;color:var(--ink)}
.services .section-lead{margin-top:4px}
.service-cards{position:absolute;top:115px;left:112px;display:flex;gap:28px}
.card{background:var(--light);border:1px solid #e3e3e3;height:362px;padding:20px 22px;box-shadow:0 2px 4px rgba(0,0,0,.12)}
.card.resourcing{width:558px}
.card.management{width:390px}
.card-head{display:flex;align-items:center;gap:8px;border-bottom:1px solid var(--line);padding-bottom:10px;font-family:"Ubuntu",sans-serif;font-size:19px;color:var(--navy);text-transform:uppercase}
.card-head b{font-weight:700}
.offer{display:flex;gap:18px;margin-top:22px}
.offer .dot{flex:0 0 84px;height:84px;border-radius:50%;background:var(--blue);display:flex;align-items:center;justify-content:center}
.offer h4{font-size:15px;color:var(--blue);text-transform:uppercase}
.offer p{font-size:12px;color:var(--grey);line-height:19px}
.offer ul{list-style:none;margin-top:4px}
.offer li{font-size:12px;color:var(--grey);line-height:21px}
.offer li::before{content:"∞ ";color:var(--orange);font-weight:700}
.offer .lede{font-size:17px;line-height:25px;color:var(--blue);font-family:"Ubuntu",sans-serif}

/* dna */
.dna{height:750px;background:linear-gradient(160deg,#2a2d33,#121417);color:var(--white)}
.dna .section-title{padding-top:52px}
.dna .section-lead{color:#c0c3c8}
.dna-table{position:absolute;top:164px;left:112px;width:976px;background:var(--white);color:var(--ink);border-collapse:collapse}
.dna-table th{height:109px;font-family:"Ubuntu",sans-serif;font-weight:500;font-size:30px;text-transform:uppercase;vertical-align:middle}
.dna-table th small{display:block;font-size:13px;margin-top:4px;text-transform:uppercase}
.dna-table th.resource{width:476px;background:var(--orange);color:var(--white)}
.dna-table th.resource small{text-transform:none;font-size:16px}
.dna-table th.gold,.dna-table th.platinum{width:250px;background:#1c1f25;color:var(--white)}
.dna-table th.gold{border-right:1px solid #444}
.dna-table td{height:41px;border-bottom:1px solid var(--line);font-size:12px;padding-left:22px}
.dna-table td.mark{padding:0;text-align:center;border-left:1px solid var(--line);color:var(--orange);font-size:16px}
.dna-table tr:nth-child(odd) td{background:#f7f7f7}
.dna-table tr.signup td{height:68px;background:var(--white);border-bottom:0}
.btn-signup{display:inline-block;background:var(--navy-deep);color:var(--white);font-size:12px;font-weight:700;padding:9px 26px;text-transform:uppercase}

/* technology */
.technology{height:473px;background:var(--white)}
.technology .section-title{padding-top:50px}
.skills{position:absolute;top:166px;left:112px;width:976px;display:flex}
.skill{flex:1;text-align:center;border-right:1px solid var(--line);padding:0 20px;height:240px}
.skill:last-child{border-right:0}
.skill .icon{width:108px;height:108px;border-radius:50%;background:var(--blue);margin:0 auto;display:flex;align-items:center;justify-content:center}
.skill h3{font-size:16px;color:var(--blue);text-transform:uppercase;margin-top:14px}
.skill .sub{font-size:12px;color:var(--grey);margin-top:4px}
.skill ul{list-style:none;margin-top:8px;display:inline-block;text-align:left}
.skill li{font-size:12px;color:var(--grey);line-height:23px}
.skill li::before{content:"∞ ";color:var(--orange);font-weight:700}

/* delivery */
.delivery{height:506px;background:linear-gradient(180deg,#1c2026,#2a2e34 60%,#15171b);color:var(--white)}
.delivery .section-title{padding-top:40px}
.delivery .section-lead{color:#c0c3c8;margin-top:8px}
.timeline{position:absolute;left:0;top:0;width:1200px;height:506px}
.step{position:absolute;width:76px;height:76px;border-radius:50%;background:var(--blue);border:4px solid #8fc0f2;top:250px;display:flex;align-items:center;justify-content:center;font-family:"Ubuntu",sans-serif;font-size:30px;color:var(--white)}
.callout{position:absolute;background:var(--white);color:var(--ink);padding:12px 14px;width:230px;font-size:12px;line-height:19px}
.callout h4{font-size:12px;color:var(--navy);text-transform:uppercase;margin-bottom:4px}

/* about */
.about{height:491px;background:var(--white)}
.about .section-title{padding-top:44px}
.about .section-lead{margin-top:8px}
.team{position:absolute;top:196px;left:112px;width:976px;display:flex;justify-content:space-between}
.member{width:470px;text-align:center}
.member .photo{width:110px;height:110px;border-radius:50%;margin:0 auto;background:linear-gradient(160deg,#c9ccd1,#6f747c)}
.member h3{font-size:15px;color:var(--blue);text-transform:uppercase;margin-top:14px}
.member p{font-size:12px;color:var(--grey);line-height:20px;margin-top:8px}
.about-close{position:absolute;top:444px;width:100%;text-align:center;font-size:12px;color:var(--ink)}

/* contact */
.contact{height:538px;background:linear-gradient(160deg,#262a30,#0f1114);color:var(--white)}
.contact .section-title{padding-top:48px}
.contact .section-lead{color:#c0c3c8;margin-top:6px}
.details{position:absolute;top:180px;left:164px;list-style:none}
.details li{display:flex;align-items:center;gap:18px;height:68px;font-size:15px}
.details .ic{width:40px;height:40px;border-radius:50%;background:var(--white);display:flex;align-items:center;justify-content:center}
.social{position:absolute;top:394px;left:164px;display:flex;gap:9px}
.social span{width:32px;height:32px;border-radius:50%}
.contact-form{position:absolute;top:180px;left:682px;width:406px}
.contact-form .field{height:52px;border:2px solid var(--blue);background:#0b0c0e;margin-bottom:16px;padding:0 16px;display:flex;align-items:center;font-size:13px;color:#c8c8c8}
.btn-submit{display:inline-block;margin-left:94px;background:var(--orange);color:var(--white);font-size:12px;font-weight:700;padding:12px 42px;text-transform:uppercase}

/* footer */
.site-footer{height:45px;background:#0e0f12;color:#7a7d82;font-size:11px;display:flex;align-items:center;justify-content:space-between;padding:0 112px}
</style>
</head>
<body>

<header class="site-header">
  <div class="brand"><span class="brand-name">vantyx</span><span class="brand-tag">IT resourcing</span></div>
  <nav class="nav">
    <a href="#home" class="active">Home</a><a href="#services">Services</a><a href="#dna">Our DNA</a><a href="#competence">Competencies</a><a href="#delivery">Delivery</a><a href="#about">About us</a><a href="#contact">Contact</a>
  </nav>
</header>

<section class="hero" id="home" role="img" aria-label="Sunset over a rocky seashore">
  <div class="hero-lines">
    <p><span>∞</span>Charge less, for doing more</p>
    <p><span>∞</span>Always deliver<span>∞</span></p>
    <p><span>∞</span>Bring some rigour<span>∞</span></p>
  </div>
  <div class="hero-dots"><i></i><i class="on"></i><i></i></div>
</section>

<section class="iteration">
  <h2 class="section-title">An iteration of traditional resourcing</h2>
  <p class="section-lead">In a market where outstanding people are hard to find, we wanted to offer a solution:</p>
  <div class="benefits">
    <div class="benefit">
      <svg class="icon" viewBox="0 0 96 96"><circle cx="48" cy="48" r="46" fill="var(--blue)"/><circle cx="48" cy="48" r="26" fill="none" stroke="#fff" stroke-width="5"/><path d="M48 30v19l12 8" fill="none" stroke="#fff" stroke-width="5" stroke-linecap="round"/></svg>
      <h3>Time to hire</h3>
      <p>Combine local market coverage, with access to global markets to deliver exceptional people quickly.</p>
    </div>
    <div class="benefit">
      <svg class="icon" viewBox="0 0 96 96"><circle cx="48" cy="48" r="46" fill="var(--blue)"/><text x="48" y="62" text-anchor="middle" font-family="Ubuntu,sans-serif" font-size="42" font-weight="700" fill="#fff">£</text></svg>
      <h3>Cost to hire</h3>
      <p>Reduce cost per hire by sharing the financial benefits of resourcing more efficiently together.</p>
    </div>
    <div class="benefit">
      <svg class="icon" viewBox="0 0 96 96"><circle cx="48" cy="48" r="46" fill="var(--blue)"/><circle cx="48" cy="48" r="24" fill="#fff"/><path d="M37 48l8 8 15-16" fill="none" stroke="#3aa34a" stroke-width="6" stroke-linecap="round" stroke-linejoin="round"/></svg>
      <h3>Quality of hires</h3>
      <p>Bring IT service delivery quality to the resourcing process, to assure the quality of hires.</p>
    </div>
  </div>
</section>

<section class="services" id="services">
  <h2 class="section-title">Our services</h2>
  <p class="section-lead">Our focus is on saving you time and money on your IT resourcing, without compromising quality.</p>
  <div class="service-cards">
    <div class="card resourcing">
      <div class="card-head"><b>vantyx</b> Resourcing</div>
      <div class="offer">
        <div class="dot"><svg width="40" height="40" viewBox="0 0 40 40"><circle cx="20" cy="15" r="8" fill="#fff"/><path d="M20 38 10 20h20z" fill="#fff"/></svg></div>
        <div><h4>Local</h4><p>High quality IT resources delivered on-site.</p><ul><li>Permanent or contract hires</li></ul></div>
      </div>
      <div class="offer">
        <div class="dot"><svg width="44" height="44" viewBox="0 0 44 44"><circle cx="22" cy="22" r="18" fill="none" stroke="#fff" stroke-width="3"/><path d="M4 22h36M22 4c-8 10-8 26 0 36M22 4c8 10 8 26 0 36" fill="none" stroke="#fff" stroke-width="2"/></svg></div>
        <div><h4>Global</h4><p>Access to global markets to deliver hard to find resources:</p><ul><li>High quality IT resourcing delivered from Eastern Europe.</li><li>Near shoring – Permanent, flexible and project delivery solutions.</li><li>On shoring – Bringing global resources to the UK.</li></ul></div>
      </div>
    </div>
    <div class="card management">
      <div class="card-head"><b>vantyx</b> Resourcing management</div>
      <div class="offer">
        <div class="dot"><svg width="40" height="40" viewBox="0 0 40 40"><rect x="9" y="6" width="22" height="28" rx="2" fill="#fff"/><path d="M14 20l5 5 8-9" fill="none" stroke="var(--blue)" stroke-width="3"/></svg></div>
        <div><p class="lede">Take responsibility for some or all of your IT recruitment process.</p><ul><li>The greater responsibility, the lower the cost.</li><li>Maximise hiring cost and time savings from time to hire, lower churn, and improved candidate experience.</li><li>No service charge AND lower rates to affect efficiencies.</li></ul></div>
      </div>
    </div>
  </div>
</section>

<section class="dna" id="dna">
  <h2 class="section-title">Our DNA</h2>
  <p class="section-lead">vantyx RESOURCE is our best practice resourcing toolset.Included every time. Defined, proven, measurable processes.<br>Assuring resource quality, time and cost.</p>
  <table class="dna-table">
    <tr><th class="resource">Resource<small>Your Best Practice Toolset</small></th><th class="gold">Gold<small>Standard</small></th><th class="platinum">Platinum<small>Options</small></th></tr>
    <tr><td>Workforce Planning</td><td class="mark"></td><td class="mark">✔</td></tr>
    <tr><td>Process audit and design</td><td class="mark"></td><td class="mark">✔</td></tr>
    <tr><td>Candidate experience mapping</td><td class="mark">✔</td><td class="mark"></td></tr>
    <tr><td>Candidate SPecification &amp; Profiling</td><td class="mark">✔</td><td class="mark"></td></tr>
    <tr><td>Candidate Attraction</td><td class="mark">✔</td><td class="mark">✔</td></tr>
    <tr><td>Candidate Relationship Management</td><td class="mark">✔</td><td class="mark"></td></tr>
    <tr><td>Technical and behavioral evaluation</td><td class="mark"></td><td class="mark">✔</td></tr>
    <tr><td>On-Shoring of global resources to UK</td><td class="mark"></td><td class="mark">✔</td></tr>
    <tr><td>vantyx Service Levels &amp; Penalties</td><td class="mark">✔</td><td class="mark"></td></tr>
    <tr class="signup"><td></td><td class="mark"><span class="btn-signup">Signup now</span></td><td class="mark"><span class="btn-signup">Signup now</span></td></tr>
  </table>
</section>

<section class="technology" id="competence">
  <h2 class="section-title">Technology competence</h2>
  <p class="section-lead">We have proven experience in hiring IT resourcing both as a resourcing partner, and in<br>complex global enterprise operational environments.</p>
  <div class="skills">
    <div class="skill">
      <div class="icon"><svg width="60" height="52" viewBox="0 0 60 52"><rect x="3" y="3" width="54" height="36" rx="2" fill="#5bbf3a" stroke="#fff" stroke-width="3"/><rect x="24" y="40" width="12" height="7" fill="#fff"/><rect x="16" y="46" width="28" height="4" fill="#fff"/></svg></div>
      <h3>Software development</h3><p class="sub">Roles across entire SDLC</p>
      <ul><li>Desktop, web &amp; enterprise solutions</li><li>Kavo, C#, C++</li><li>Rubel, Hypr, Pytha, Scriptly</li></ul>
    </div>
    <div class="skill">
      <div class="icon"><svg width="40" height="60" viewBox="0 0 40 60"><rect x="4" y="2" width="32" height="56" rx="5" fill="#fff"/><rect x="8" y="9" width="24" height="40" fill="#2d6fd0"/><circle cx="20" cy="53" r="2.5" fill="#2d6fd0"/></svg></div>
      <h3>Mobile applications</h3><p class="sub">Role across entire SDLC</p>
      <ul><li>Droidline</li><li>Orbit OS</li><li>Paneworks Mobile</li></ul>
    </div>
    <div class="skill">
      <div class="icon"><svg width="64" height="44" viewBox="0 0 64 44"><circle cx="16" cy="14" r="7" fill="#fff"/><circle cx="48" cy="14" r="7" fill="#fff"/><circle cx="32" cy="12" r="9" fill="#fff"/><path d="M4 40c0-10 6-16 12-16s12 6 12 16zM36 40c0-10 6-16 12-16s12 6 12 16z" fill="#fff"/><path d="M18 42c0-12 6-19 14-19s14 7 14 19z" fill="#fff"/></svg></div>
      <h3>Senior appointments</h3><p class="sub">&nbsp;</p>
      <ul><li>CTO &amp; Development Directors</li><li>Development, Project &amp; Product Managers</li><li>Programme, Service Delivery Management /<br>&nbsp;&nbsp;&nbsp;Directorship (SMF)</li></ul>
    </div>
  </div>
</section>

<section class="delivery" id="delivery">
  <h2 class="section-title">Our delivery</h2>
  <p class="section-lead">If you were delivering a customer IT project you'd do it like this. Why would you not get your resourcing services delivered the same way ?</p>
  <div class="timeline">
    <svg width="1200" height="506" style="position:absolute;left:0;top:0"><line x1="220" y1="288" x2="1010" y2="288" stroke="#8fc0f2" stroke-width="2"/><line x1="220" y1="288" x2="220" y2="365" stroke="#fff"/><line x1="476" y1="240" x2="476" y2="180" stroke="#fff"/><line x1="726" y1="288" x2="726" y2="365" stroke="#fff"/><line x1="976" y1="240" x2="976" y2="180" stroke="#fff"/></svg>
    <div class="step" style="left:182px">1</div>
    <div class="step" style="left:438px">2</div>
    <div class="step" style="left:688px">3</div>
    <div class="step" style="left:938px">4</div>
    <div class="callout" style="left:359px;top:138px"><h4>Kick-off</h4>We review the project and set it up to ensure success.</div>
    <div class="callout" style="left:866px;top:138px"><h4>Service management</h4>Offering full transparency and control over your service.</div>
    <div class="callout" style="left:116px;top:364px"><h4>Your requirements defined</h4>Define and agree your requirements in a Statement of Work.</div>
    <div class="callout" style="left:612px;top:364px"><h4>Delivery</h4>We deliver your services: vantyx Resourcing Management.</div>
  </div>
</section>

<section class="about" id="about">
  <h2 class="section-title">About us</h2>
  <p class="section-lead">We created vantyx because we wanted to offer something different in IT resourcing.<br>We're expert at what we do, with a track record of IT Service Delivery and Resourcing excellence in high growth environments:</p>
  <div class="team">
    <div class="member">
      <div class="photo" role="img" aria-label="Portrait of Marcus Ellery"></div>
      <h3>Marcus Ellery</h3>
      <p>With a background in sales management and recruitment, Marcus founded a highly successful recruitment agency and built it into one of the UK's leading specialist agencies. Successfully exiting the business after</p>
    </div>
    <div class="member">
      <div class="photo" role="img" aria-label="Portrait of Tobias Wrenfield"></div>
      <h3>Tobias Wrenfield</h3>
      <p>With a history in telecoms and IT services, Tobias has held many senior level positions from marketing to operations. His last role was as COO for an IT services company, supporting the growth from 250 to 2000 people whilst</p>
    </div>
  </div>
  <p class="about-close">One of our core aims with vantyx is to build a fantastic team. Happy team, happy customers, successful business !</p>
</section>

<section class="contact" id="contact">
  <h2 class="section-title">Contact</h2>
  <p class="section-lead">If you think we can help, we'd love to hear from you.</p>
  <ul class="details">
    <li><span class="ic"><svg width="18" height="18" viewBox="0 0 18 18"><rect x="5" y="1" width="8" height="16" rx="2" fill="none" stroke="#222" stroke-width="2"/></svg></span>1-4410-552-019</li>
    <li><span class="ic"><svg width="20" height="16" viewBox="0 0 20 16"><rect x="1" y="1" width="18" height="14" fill="none" stroke="#222" stroke-width="2"/><path d="M1 1l9 8 9-8" fill="none" stroke="#222" stroke-width="2"/></svg></span>hello@vantyx.io</li>
    <li><span class="ic"><svg width="16" height="20" viewBox="0 0 16 20"><path d="M8 19S1 11 1 7a7 7 0 0 1 14 0c0 4-7 12-7 12z" fill="#222"/><circle cx="8" cy="7" r="2.5" fill="#fff"/></svg></span>2 Lorem Ipsum , Lorem Ipsum, loremipsum - 123 456</li>
  </ul>
  <div class="social"><span style="background:#3b5998"></span><span style="background:#1da1f2"></span><span style="background:#dd4b39"></span><span style="background:#cc181e"></span><span style="background:#f26522"></span><span style="background:#3aa34a"></span></div>
  <div class="contact-form">
    <div class="field">Name</div>
    <div class="field">Email Address</div>
    <div class="field">Text</div>
    <span class="btn-submit">Submit</span>
  </div>
</section>

<footer class="site-footer"><span>Copyright © 2014 vantyx. All Right Reserved.</span><span>Privacy Statement | Terms &amp; Conditions</span></footer>

</body>
</html>
```